Alcohol brand needs design for gift tin packaging

We need a new design for the gift tins for our vodka brand. The bottles are in the shape of an oil barrel and the tins are also in the same shape. We would like to see the use of our logo. The gift tin needs to have a premium look.
Images of our bottles, logo and the gift tin are attached.

```html
<!DOCTYPE html>
<html lang="en">
<head>
<meta charset="UTF-8">
<title>Iron Drum Vodka – Gift Tin Wrap</title>
<link href="https://fonts.googleapis.com/css2?family=Bebas+Neue&display=swap" rel="stylesheet">
<style>
  :root {
    --page-bg: #e9e7e3;
    --steel-light: #f4f4f4;
    --steel-mid: #c9c9c9;
    --steel-dark: #8a8a8a;
    --rib-dark: #3a3a3a;
    --rib-light: #d8d8d8;
    --gold-light: #f2b640;
    --gold-deep: #b8730f;
    --ink: #111111;
  }
  html, body {
    margin: 0;
    padding: 0;
    width: 1200px;
    height: 800px;
    overflow: hidden;
    background: var(--page-bg);
    font-family: "Bebas Neue", "Arial Narrow", sans-serif;
  }
  .canvas {
    position: relative;
    width: 1200px;
    height: 800px;
    display: flex;
    align-items: center;
    justify-content: center;
  }
  .tin-wrap {
    position: relative;
    width: 760px;
    height: 720px;
    background:
      linear-gradient(90deg, var(--steel-dark) 0%, var(--steel-light) 22%, var(--steel-mid) 50%, var(--steel-light) 78%, var(--steel-dark) 100%);
    border-radius: 6px;
    display: grid;
    grid-template-rows: 1fr 16px 1.4fr 16px 1.25fr;
    box-shadow: 0 10px 30px rgba(0,0,0,0.18);
  }
  .rib {
    background: linear-gradient(180deg, var(--rib-light) 0%, var(--rib-dark) 45%, var(--rib-light) 100%);
    border-radius: 8px;
    margin: 0 -10px;
  }
  .band {
    display: flex;
    align-items: center;
    justify-content: center;
    position: relative;
  }
  .gold {
    background: linear-gradient(180deg, var(--gold-light), var(--gold-deep));
    -webkit-background-clip: text;
    background-clip: text;
    color: transparent;
  }
  .brand-title {
    font-size: 150px;
    letter-spacing: 6px;
    line-height: 1;
    margin: 0;
  }
  .band-middle {
    justify-content: space-between;
    padding: 0 90px;
  }
  .side-note {
    font-size: 54px;
    line-height: 0.95;
    text-align: center;
    white-space: nowrap;
    margin: 0;
    padding: 0 4px;
  }
  .brand-mark {
    display: flex;
    flex-direction: column;
    align-items: center;
    gap: 14px;
  }
  .brand-mark-dot {
    width: 130px;
    height: 130px;
    border-radius: 50%;
    background: var(--ink);
  }
  .brand-mark-name {
    font-size: 44px;
    letter-spacing: 3px;
    color: var(--ink);
    white-space: nowrap;
  }
  .band-bottom {
    flex-direction: column;
  }
  .product-name {
    font-size: 170px;
    line-height: 0.9;
    letter-spacing: 4px;
    color: var(--ink);
    margin: 0;
  }
  .tagline {
    font-size: 50px;
    letter-spacing: 3px;
    line-height: 1;
    margin: 6px 0 0;
  }
</style>
</head>
<body>
  <main class="canvas">
    <section class="tin-wrap">
      <div class="band band-top">
        <h1 class="brand-title gold">Iron Drum</h1>
      </div>
      <div class="rib"></div>
      <div class="band band-middle">
        <p class="side-note gold">Since<br>2017</p>
        <div class="brand-mark" role="img" aria-label="Iron Drum brand mark">
          <span class="brand-mark-dot"></span>
          <span class="brand-mark-name">Iron Drum</span>
        </div>
        <p class="side-note gold">40%<br>Alcohol</p>
      </div>
      <div class="rib"></div>
      <div class="band band-bottom">
        <h2 class="product-name">Vodka</h2>
        <p class="tagline gold">Drink Cautiously</p>
      </div>
    </section>
  </main>
</body>
</html>
```